Local Roofing/Construction company business needs new biz card design

We need a new business card design, current cards are from the start of this operation and generic at best. We are a local Construction Company (General Contractor) with a majority of our work originating from insurance claims-exterior finish work is the main focus (Roofs-Siding-Gutters etc). Heavily involved with homeowners and the low ball offers they receive from insurance company's after a insurable event takes place. I have attached some of our original logo file(s) below.

```html
<!DOCTYPE html>
<html lang="en">
<head>
<meta charset="utf-8">
<title>Stonefield Builders – Business Card</title>
<link href="https://fonts.googleapis.com/css2?family=Poppins:wght@300;400;600&display=swap" rel="stylesheet">
<style>
  :root {
    --page-bg: #0d0d0e;
    --card-bg: #28292b;
    --card-back-bg: #232426;
    --badge-bg: #0f1e1e;
    --accent: #2fd67a;
    --text-light: #d6d6d6;
    --text-white: #f4f4f4;
    --rule: #4a4b4e;
    --faint-mark: #3a3b3e;
  }
  * { box-sizing: border-box; margin: 0; padding: 0; }
  html, body { width: 1200px; height: 820px; overflow: hidden; }
  body {
    background: var(--page-bg);
    font-family: "Poppins", sans-serif;
    display: flex;
    align-items: center;
    justify-content: center;
    gap: 40px;
  }
  .card {
    position: relative;
    width: 540px;
    height: 310px;
    border-radius: 3px;
  }
  .card-front {
    background: var(--card-bg);
    border-left: 3px solid var(--accent);
    border-bottom: 3px solid var(--accent);
  }
  .brand-badge {
    position: absolute;
    top: 34px;
    right: 40px;
    height: 76px;
    padding: 0 34px;
    background: var(--badge-bg);
    clip-path: polygon(14px 0, calc(100% - 14px) 0, 100% 14px, 100% calc(100% - 14px), calc(100% - 14px) 100%, 14px 100%, 0 calc(100% - 14px), 0 14px);
    display: flex;
    align-items: center;
    gap: 14px;
  }
  .brand-square {
    width: 30px;
    height: 30px;
    background: var(--accent);
  }
  .brand-name {
    font-weight: 600;
    font-size: 24px;
    letter-spacing: 1.5px;
    text-transform: uppercase;
    color: var(--text-white);
    line-height: 1;
  }
  .rule-top {
    position: absolute;
    top: 128px;
    left: 200px;
    right: 40px;
    height: 1px;
    background: var(--rule);
  }
  .person {
    position: absolute;
    left: 38px;
    top: 146px;
  }
  .person-name {
    color: var(--accent);
    font-weight: 600;
    font-size: 18px;
    letter-spacing: 0.5px;
    text-transform: uppercase;
    line-height: 1.1;
  }
  .person-title {
    color: var(--text-light);
    font-weight: 400;
    font-size: 14px;
  }
  .rule-mid {
    position: absolute;
    top: 196px;
    left: 38px;
    width: 230px;
    height: 1px;
    background: var(--rule);
  }
  .contact-list {
    position: absolute;
    left: 38px;
    top: 208px;
    list-style: none;
  }
  .contact-list li {
    display: flex;
    align-items: center;
    gap: 9px;
    color: var(--text-light);
    font-size: 13.5px;
    font-weight: 300;
    line-height: 26px;
  }
  .contact-icon { width: 13px; height: 13px; flex: none; }
  .address {
    position: absolute;
    right: 40px;
    top: 176px;
    text-align: right;
    color: var(--text-light);
    font-size: 13.5px;
    font-weight: 300;
    line-height: 1.45;
  }
  .card-back {
    background: var(--card-back-bg);
    border-right: 3px solid var(--accent);
    border-bottom: 3px solid var(--accent);
    display: flex;
    align-items: center;
    justify-content: center;
  }
  .back-mark {
    font-weight: 600;
    font-size: 44px;
    letter-spacing: 3px;
    text-transform: uppercase;
    color: var(--faint-mark);
  }
</style>
</head>
<body>
  <section class="card card-front">
    <div class="brand-badge">
      <span class="brand-square"></span>
      <span class="brand-name">Stonefield Builders</span>
    </div>
    <div class="rule-top"></div>

    <div class="person">
      <p class="person-name">Marcus Hale</p>
      <p class="person-title">Managing Director</p>
    </div>
    <div class="rule-mid"></div>

    <ul class="contact-list">
      <li>
        <svg class="contact-icon" viewBox="0 0 24 24" aria-hidden="true"><path fill="var(--accent)" d="M6.6 10.8a15.1 15.1 0 0 0 6.6 6.6l2.2-2.2a1 1 0 0 1 1-.25 11.4 11.4 0 0 0 3.6.57 1 1 0 0 1 1 1V20a1 1 0 0 1-1 1A17 17 0 0 1 3 4a1 1 0 0 1 1-1h3.5a1 1 0 0 1 1 1c0 1.25.2 2.45.57 3.57a1 1 0 0 1-.25 1z"/></svg>
        044-555 210 348
      </li>
      <li>
        <svg class="contact-icon" viewBox="0 0 24 24" aria-hidden="true"><path fill="var(--accent)" d="M2 5h20v14H2zm2 2v.5l8 5 8-5V7zm0 2.9V17h16V9.9l-8 5z"/></svg>
        hello@stonefield.com
      </li>
      <li>
        <svg class="contact-icon" viewBox="0 0 24 24" aria-hidden="true"><circle cx="12" cy="12" r="9.5" fill="none" stroke="var(--accent)" stroke-width="2"/><path d="M2.5 12h19M12 2.5c3 3 3 16 0 19M12 2.5c-3 3-3 16 0 19" fill="none" stroke="var(--accent)" stroke-width="1.6"/></svg>
        www.stonefield.com
      </li>
    </ul>

    <p class="address">87 Quarry Road, Eastvale<br>30718, Northland</p>
  </section>

  <section class="card card-back">
    <span class="back-mark">Stonefield</span>
  </section>
</body>
</html>
```